Family business needs stationery redesign with new logo

Family owned company, established in 1987 wanting a brand 'refresh'. We are an electrical, refrigeration and construction company based in the Barkly Region Northern Territory, Australia. We have a new logo we would like to use which is uploaded along with our current letterhead and email signature. We are also dropping the word 'contractors' so please do not include this on any designs. Please note also, the 'orange' color used in our logo and designs should be Northern Territory red ochre which is as follows:

RGB (Hex): #C75B12
PantoneĀ® 159 C
CMYK: 1 / 74 / 100 / 7

We are needing our stationery redesigned using our new logo. Please include letterheads, business cards, envelopes, and email signatures.

We currently use our business letterheads for quotations, invoices, letters, HR matters, and internal memos.

We also need a separate simplified letterhead for internal paperwork such as employee leave forms, meeting agendas, and meeting minutes etc.

Reason: Needing more submissions of full package designs. We are wanting all our stationery, including business cards, letterheads, email signatures, envelopes, etc to be cohesive. We also require ALL the information, as supplied on our template letterhead, to be included on the new letterhead designs. including electrical license no.etc Thank you, R&W

Reason: needing more time as work has got in the way of looking over designs. A lot of designs not meeting the brief/criteria.

Industry/Entity Type

Business

Colors
0355a3
f37122

Requirements
Must have
• The 'orange' color used in the designs should be Northern Territory red ochre which is as follows:
• RGB (Hex): #C75B12
• PantoneĀ® 159 C
• CMYK: 1 / 74 / 100 / 7
• ***MUST INCLUDE ALL INFORMATION THAT IS ON OUR CURRENT LETTERHEAD***
Should not have
• Please do not include the word 'contractors'

```html
<!DOCTYPE html>
<html lang="en">
<head>
<meta charset="utf-8">
<title>R&amp;W Business Card</title>
<link rel="stylesheet" href="https://fonts.googleapis.com/css2?family=Source+Sans+3:wght@400;600&display=swap">
<style>
  :root {
    --navy: #1b3170;
    --ochre: #c75b12;
    --paper: #ffffff;
    --ink: #4a4a4a;
    --backdrop: #e4e4e4;
  }
  html, body {
    margin: 0;
    width: 1200px;
    height: 987px;
    overflow: hidden;
    background: var(--backdrop);
    font-family: "Source Sans 3", "Myriad Pro", Arial, sans-serif;
  }
  .canvas { position: relative; width: 1200px; height: 987px; }
  .card {
    position: absolute;
    left: 293px;
    width: 615px;
    height: 350px;
    border-radius: 20px;
    overflow: hidden;
    box-shadow: 0 2px 5px rgba(0,0,0,0.25);
  }
  .card--front { top: 130px; background: var(--paper); }
  .card--back { top: 505px; background: var(--ochre); }

  .wordmark {
    position: absolute;
    left: 0; right: 0;
    text-align: center;
    font-weight: 600;
    font-size: 88px;
    line-height: 1;
    letter-spacing: 1px;
    white-space: nowrap;
  }
  .card--front .wordmark { top: 56px; color: var(--navy); }
  .card--back .wordmark { top: 131px; color: var(--paper); }

  .tab { position: absolute; top: 230px; width: 9px; height: 93px; }
  .tab--left { left: 0; background: var(--navy); border-radius: 0 6px 6px 0; }
  .tab--right { right: 0; width: 13px; background: var(--ochre); border-radius: 6px 0 0 6px; }

  .identity { position: absolute; left: 38px; top: 226px; white-space: nowrap; }
  .identity__name { margin: 0; font-size: 22px; font-weight: 600; color: var(--navy); line-height: 1.1; }
  .identity__role { margin: 3px 0 7px; font-size: 16.5px; color: var(--ochre); line-height: 1.2; }
  .identity__address { margin: 0; font-size: 16px; color: var(--ink); line-height: 23px; font-style: normal; }

  .contacts { position: absolute; right: 33px; top: 228px; margin: 0; padding: 0; list-style: none; white-space: nowrap; }
  .contacts li {
    display: flex; justify-content: flex-end; align-items: center;
    font-size: 16px; color: var(--ink); line-height: 23.5px;
  }
  .contacts svg { width: 15px; height: 15px; margin-left: 7px; fill: var(--navy); flex: none; }

  .established {
    position: absolute; left: 0; right: 0; top: 294px;
    text-align: center; color: var(--paper);
    font-size: 15.5px; letter-spacing: 2px;
  }
</style>
</head>
<body>
<div class="canvas">
  <section class="card card--front">
    <div class="wordmark">R&amp;W</div>
    <span class="tab tab--left"></span>
    <span class="tab tab--right"></span>
    <div class="identity">
      <h1 class="identity__name">DANIEL HARPER</h1>
      <p class="identity__role">CEO/FOUNDER</p>
      <address class="identity__address">4120 Ridgeview Road<br>Tennant Creek, NT 0860</address>
    </div>
    <ul class="contacts">
      <li>614 208 3391
        <svg viewBox="0 0 16 16" aria-hidden="true"><path d="M3.5 1.5l2.5 0 1.2 3.2-1.6 1.2c.8 1.8 2.2 3.2 4 4l1.2-1.6 3.2 1.2v2.5c0 .8-.7 1.5-1.5 1.5C6.8 13.5 2 8.7 2 3c0-.8.7-1.5 1.5-1.5z"/></svg>
      </li>
      <li>614 208 3392
        <svg viewBox="0 0 16 16" aria-hidden="true"><path d="M4 1h8v4H4zM1 6h14v6h-3v3H4v-3H1zM5 10v4h6v-4z"/></svg>
      </li>
      <li>office@rwgroup.com
        <svg viewBox="0 0 16 16" aria-hidden="true"><path d="M1 3h14v10H1zM2.5 4.5 8 9l5.5-4.5z" fill-rule="evenodd"/></svg>
      </li>
      <li>www.rwgroup.com
        <svg viewBox="0 0 16 16" aria-hidden="true"><circle cx="8" cy="8" r="7"/><path d="M5 4c1.5 0 2 1 3 1.5S7 8 5.5 8 4 6 5 4zM10 9c1 0 2 1 1.5 2.5S9 13 9 11.5 9 9 10 9z" fill="#fff"/></svg>
      </li>
    </ul>
  </section>

  <section class="card card--back">
    <div class="wordmark">R&amp;W</div>
    <div class="established">Est. 1987</div>
  </section>
</div>
</body>
</html>
```